Stylish new business card needed!

Hello everyone! I am in need of a new business card design for an alarm company here in Hurricane WV. I have all fonts, color codes and logos provided for you use! We are a young company and like the style of a clean sleek looking business card. Would like it double sided, one side holding the logo and the other with your design!
Target Market(s)
The people that are looking for the newest tech for home automation and security
Industry/Entity Type
Alarm services; Home automation
Contact Information for Business Card
Name of person; position (Sales; Installer); Phone Number (555.418.7260); Employee cell Number; Website (www.GuardedByVelk.example); Employee Email; Double sided
Look and feel
Each slider illustrates characteristics of the customer's brand and the style your logo design should communicate.

```html
<!DOCTYPE html>
<html lang="en">
<head>
<meta charset="utf-8">
<title>Velk Business Card</title>
<link rel="stylesheet" href="https://fonts.googleapis.com/css2?family=Montserrat:wght@400;500;700&display=swap">
<style>
  :root {
    --backdrop: #d3d6d6;
    --card-white: #f7f7f6;
    --card-grey: #8b8b8b;
    --accent: #d9661f;
    --ink: #4a4a4a;
    --ink-soft: #5e5e5e;
    --emboss: #e9e9e9;
  }
  * { margin: 0; padding: 0; box-sizing: border-box; }
  html, body { width: 1200px; height: 829px; overflow: hidden; }
  body {
    background: var(--backdrop);
    font-family: "Montserrat", Arial, sans-serif;
    color: var(--ink);
    position: relative;
  }
  .card {
    position: absolute;
    top: 260px;
    width: 540px;
    height: 309px;
    border-radius: 3px;
    box-shadow: 0 14px 30px rgba(0,0,0,0.18);
  }
  .card--front { left: 50px; background: var(--card-white); }
  .card--back {
    left: 610px;
    background: var(--card-grey);
    display: flex;
    align-items: center;
    justify-content: center;
  }
  .name-bar {
    position: absolute;
    left: 26px; top: 30px;
    width: 11px; height: 30px;
    background: var(--accent);
  }
  .identity { position: absolute; left: 48px; top: 29px; }
  .identity__name {
    color: var(--accent);
    font-weight: 700;
    font-size: 17px;
    letter-spacing: 1.2px;
    text-transform: uppercase;
    line-height: 1.1;
  }
  .identity__role { font-size: 12px; color: var(--ink-soft); margin-top: 3px; }
  .contacts {
    position: absolute;
    left: 26px; top: 150px;
    list-style: none;
    font-size: 12.5px;
    letter-spacing: 0.3px;
  }
  .contacts li { display: flex; align-items: center; gap: 8px; margin-bottom: 9px; }
  .contacts svg { width: 11px; height: 11px; flex: none; }
  .brand {
    position: absolute;
    right: 40px; top: 128px;
    display: flex;
    align-items: center;
    gap: 12px;
  }
  .brand__dot { width: 14px; height: 14px; border-radius: 50%; background: var(--accent); }
  .brand__name {
    font-weight: 500;
    font-size: 54px;
    letter-spacing: 3px;
    color: var(--ink);
  }
  .address {
    position: absolute;
    right: 30px; bottom: 24px;
    text-align: right;
    font-size: 12.5px;
    line-height: 1.55;
    letter-spacing: 0.3px;
  }
  .back-brand {
    font-weight: 500;
    font-size: 100px;
    letter-spacing: 6px;
    color: var(--emboss);
  }
</style>
</head>
<body>
  <section class="card card--front" aria-label="Business card front">
    <div class="name-bar"></div>
    <div class="identity">
      <p class="identity__name">Dana Porter</p>
      <p class="identity__role">Sales/Installer</p>
    </div>
    <ul class="contacts">
      <li>
        <svg viewBox="0 0 12 12" aria-hidden="true"><path d="M2.5 1h2l1 3-1.3 1a6 6 0 0 0 2.8 2.8L8 6.5l3 1v2A1.5 1.5 0 0 1 9.5 11 8.5 8.5 0 0 1 1 2.5 1.5 1.5 0 0 1 2.5 1z" fill="var(--accent)"/></svg>
        555.418.7260
      </li>
      <li>
        <svg viewBox="0 0 12 12" aria-hidden="true"><rect x="0.5" y="2" width="11" height="8" fill="var(--accent)"/><path d="M0.5 2 6 6.5 11.5 2" fill="none" stroke="var(--card-white)" stroke-width="1"/></svg>
        info@GuardedByVelk.example
      </li>
      <li>
        <svg viewBox="0 0 12 12" aria-hidden="true"><circle cx="6" cy="6" r="5.2" fill="none" stroke="var(--accent)" stroke-width="1.2"/><path d="M1 6h10M6 1c-2.5 3-2.5 7 0 10M6 1c2.5 3 2.5 7 0 10" fill="none" stroke="var(--accent)" stroke-width="0.9"/></svg>
        www.GuardedByVelk.example
      </li>
    </ul>
    <div class="brand">
      <span class="brand__dot"></span>
      <span class="brand__name">VELK</span>
    </div>
    <address class="address" style="font-style: normal;">
      418 Ridgeview Avenue<br>
      Maple Hollow District 4170
    </address>
  </section>

  <section class="card card--back" aria-label="Business card back">
    <span class="back-brand">VELK</span>
  </section>
</body>
</html>
```